BOLD & MINIMALIST DESIGN NEEDED

We want a very bold but minimalistic business card design that is impactful and utilizes both sides of the business card. Our current logo is included for your use.

We want bold fonts and good use of negative space. We don't want the logo to overpower the design.

Target Market(s)

Professionals who are building new commercial buildings.

Industry/Entity Type

Construction

Contact Information for Business Card

Name, Title, email, office phone, cell phone, website

Font styles to use
Serif
Sans Serif

Requirements
Must have
• Bold design!

```html
<!DOCTYPE html>
<html lang="en">
<head>
<meta charset="utf-8">
<title>Ridgecrest Design + Build — Business Card</title>
<link href="https://fonts.googleapis.com/css2?family=Montserrat:wght@400;500;700&family=Oswald:wght@600&display=swap" rel="stylesheet">
<style>
  :root {
    --bg: #1b1b1b;
    --card: #2a2a2a;
    --card-edge: #232323;
    --green: #7dc42a;
    --white: #f4f4f4;
    --emboss: #3a3a3a;
  }
  * { box-sizing: border-box; margin: 0; padding: 0; }
  html, body { width: 1200px; height: 900px; overflow: hidden; }
  body {
    background: var(--bg);
    font-family: "Montserrat", sans-serif;
    color: var(--white);
    position: relative;
  }
  .card {
    position: absolute;
    left: 280px;
    width: 640px;
    height: 366px;
    background: linear-gradient(160deg, var(--card) 0%, var(--card-edge) 100%);
    overflow: hidden;
  }
  .card::after {
    content: "";
    position: absolute;
    left: 0; right: 0; bottom: 0;
    height: 7px;
    background: var(--green);
  }
  .card--front { top: 64px; }
  .card--back { top: 470px; }

  .brand-mark {
    position: absolute;
    left: 0; right: 0; top: 140px;
    text-align: center;
    font-weight: 700;
    font-size: 40px;
    letter-spacing: 1px;
    color: var(--emboss);
    line-height: 1.1;
  }
  .brand-mark small {
    display: block;
    font-size: 40px;
  }

  .brand-logo {
    position: absolute;
    left: 40px; top: 40px;
    display: flex;
    align-items: center;
    gap: 10px;
    font-weight: 700;
    font-size: 22px;
    color: var(--white);
    letter-spacing: 0.5px;
  }
  .brand-logo .square {
    width: 16px; height: 16px;
    background: var(--white);
  }

  .person {
    position: absolute;
    left: 40px; top: 136px;
  }
  .person__name {
    font-family: "Oswald", sans-serif;
    font-weight: 600;
    font-size: 40px;
    color: var(--green);
    line-height: 1;
    text-transform: uppercase;
  }
  .person__title {
    font-size: 15px;
    font-weight: 500;
    letter-spacing: 1px;
    margin-top: 6px;
  }
  .rule {
    position: absolute;
    left: 118px; top: 204px;
    width: 490px; height: 2px;
    background: var(--green);
  }

  .contacts {
    position: absolute;
    left: 40px; top: 222px;
    list-style: none;
    font-size: 15px;
    line-height: 24px;
  }
  .contacts li { display: flex; align-items: center; gap: 8px; }
  .contacts svg { width: 14px; height: 14px; flex: none; }

  .website {
    position: absolute;
    right: 34px; bottom: 30px;
    font-size: 17px;
    font-weight: 500;
    letter-spacing: 1.5px;
  }
  .website span { color: var(--green); }
</style>
</head>
<body>

<section class="card card--front" aria-label="Card front">
  <div class="brand-mark">Ridgecrest<small>Design + Build</small></div>
</section>

<section class="card card--back" aria-label="Card back">
  <div class="brand-logo"><span class="square"></span>Ridgecrest Design + Build</div>

  <div class="person">
    <h1 class="person__name">Mark Ellison</h1>
    <p class="person__title">OWNER</p>
  </div>
  <div class="rule"></div>

  <ul class="contacts">
    <li>
      <svg viewBox="0 0 24 24" aria-hidden="true"><path fill="#7dc42a" d="M6.6 10.8a15.1 15.1 0 0 0 6.6 6.6l2.2-2.2c.3-.3.7-.4 1-.2 1.1.4 2.3.6 3.6.6.6 0 1 .4 1 1V20c0 .6-.4 1-1 1A17 17 0 0 1 3 4c0-.6.4-1 1-1h3.5c.6 0 1 .4 1 1 0 1.3.2 2.5.6 3.6.1.3 0 .7-.2 1z"/></svg>
      (555) 014-2286
    </li>
    <li>
      <svg viewBox="0 0 24 24" aria-hidden="true"><path fill="#7dc42a" d="M2 9c0-2 4.5-4 10-4s10 2 10 4v2h-5V9c-1.5-.6-3.2-.9-5-.9s-3.5.3-5 .9v2H2zM6 12h12l2 8H4zm6 2a2.5 2.5 0 1 0 0 5 2.5 2.5 0 0 0 0-5z"/></svg>
      (555) 014-2286
    </li>
    <li>
      <svg viewBox="0 0 24 24" aria-hidden="true"><rect x="2.5" y="5" width="19" height="14" fill="none" stroke="#7dc42a" stroke-width="2"/><path d="M3 6l9 7 9-7" fill="none" stroke="#7dc42a" stroke-width="2"/></svg>
      ridgecrestbuild@mail.com
    </li>
  </ul>

  <p class="website">www.<span>ridgecrestbuild</span>.com</p>
</section>

</body>
</html>
```